Bramblewood Joinery Website

My client Bramblewood Joinery is looking for a redesign for a Word Press Website. Their current site is at www.bramblewoodjoinery.example They are a custom cabinet company, but also create bathroom, living room, bar and entertainment and bedroom cabinets too. They would like a design that emulates the master craftsman work they do yet a contemporary style.

Their current site was designed using Flash elements.

Target Market(s)

Home owners and builders of high end homes

Industry/Entity Type

Entertainment

Font styles to use
Serif
Decorative

Requirements
Must have
• Must show their work and logo using a contemporary style.
Nice to have
• Sliders that showcase their projects.

```html
<!DOCTYPE html>
<html lang="en">
<head>
<meta charset="utf-8">
<title>Bramblewood Joinery</title>
<link rel="stylesheet" href="https://fonts.googleapis.com/css2?family=Figtree:wght@400;500;700&display=swap">
<style>
:root{
  --header-bg:#2f2f2f;
  --header-text:#f4f4f4;
  --nav-muted:#b8b8b8;
  --frame:#474747;
  --caption-bg:rgba(28,28,28,.86);
  --card-frame:#d6d6d6;
  --news-bg:#ebebeb;
  --body-text:#5a5a5a;
  --heading:#222;
  --button:#1e1e1e;
  --footer-bg:#eeeeee;
  --footer-line:#bdbdbd;
  --send:#3fae3a;
  --accent-blue:#1e8fd6;
}
*{margin:0;padding:0;box-sizing:border-box}
html,body{width:967px;height:1200px;overflow:hidden}
body{font-family:"Figtree",sans-serif;background:#fff;position:relative;color:var(--body-text)}

.site-header{position:absolute;left:0;top:0;width:967px;height:490px;background:radial-gradient(ellipse at 50% 40%,#3a3a3a,#292929 75%)}
.brand-mark{position:absolute;left:91px;top:12px;width:80px;height:80px;border-radius:50%;border:3px solid #fff;background:#1f1f1f;display:flex;align-items:center;justify-content:center;text-align:center;color:#fff;font-size:11px;font-weight:700;line-height:13px}
.tagline{position:absolute;left:180px;top:28px;width:210px;color:var(--header-text);font-size:14.5px;line-height:18.5px;font-weight:500}
.top-nav{position:absolute;left:418px;top:31px;display:flex;gap:18px;font-size:11px;color:var(--nav-muted)}
.phone{position:absolute;left:762px;top:20px;color:#fff;display:flex;gap:9px;align-items:center}
.phone small{display:block;font-size:11.5px;line-height:14px}
.phone b{font-size:16.5px;font-weight:400}
.main-nav{position:absolute;left:417px;top:71px;display:flex;gap:26px;font-size:12.5px;color:#fff}
.main-nav span{white-space:nowrap}

.slider{position:absolute;left:89px;top:117px;width:789px;height:306px;background:var(--frame);padding:6px 9px 9px 10px}
.slide-img{width:100%;height:100%;background:linear-gradient(180deg,#7a4519 0%,#b9772f 22%,#d9a560 40%,#c4b49a 55%,#a46a2c 72%,#5a3311 100%)}
.slide-caption{position:absolute;left:10px;bottom:9px;width:447px;height:46px;background:var(--caption-bg);color:#fff;font-size:12px;line-height:46px;padding-left:13px}
.arrow{position:absolute;top:238px}
.dots{position:absolute;left:429px;top:448px;display:flex;gap:6px}
.dots i{width:12px;height:12px;border-radius:50%;background:#1c1c1c;border:1px solid #555}
.dots i.on{background:#eee}

.cards{position:absolute;top:529px;left:89px;display:flex;gap:20px}
.card{width:250px;height:166px;background:var(--card-frame);padding:7px;position:relative}
.card-img{width:100%;height:100%}
.card-cap{position:absolute;left:7px;right:7px;bottom:7px;height:41px;background:rgba(40,40,40,.8);color:#fff;text-align:center}
.card-cap b{display:block;font-size:13.5px;padding-top:5px}
.card-cap span{font-size:9.5px}

.news{position:absolute;left:89px;top:733px;width:789px;height:39px;background:var(--news-bg);display:flex;align-items:center;padding-left:19px;font-size:10.5px;color:#333}
.news b{font-size:13.5px;font-weight:500;margin-right:9px;color:#222}
.news a{position:absolute;left:612px;color:#222;font-size:11px}
.news a u{text-decoration:underline}
.news svg{position:absolute;left:742px}

.welcome{position:absolute;left:89px;top:804px;width:385px}
h2{font-size:18.5px;font-weight:400;color:var(--heading)}
h2 b{font-weight:700}
.welcome p{font-size:11.6px;line-height:14.5px;margin-top:9px}
.welcome p+p{margin-top:14.5px}
.btn{display:inline-block;margin-top:20px;background:var(--button);color:#fff;font-size:12px;padding:0 11px;height:35px;line-height:35px}

.video{position:absolute;left:500px;top:804px;width:378px}
.video-frame{margin-top:8px;background:var(--card-frame);padding:6px;height:219px;position:relative}
.video-img{width:100%;height:100%;background:linear-gradient(110deg,#6f5a3a 0%,#a99a78 22%,#e6ddca 45%,#b9a486 65%,#8c5f36 85%,#c9542c 100%)}
.side-tools{position:absolute;right:15px;top:14px;display:flex;flex-direction:column;gap:4px}
.side-tools span{width:29px;height:23px;background:rgba(30,30,30,.85);border-radius:3px;display:flex;align-items:center;justify-content:center}
.controls{position:absolute;left:13px;right:13px;bottom:13px;height:20px;background:rgba(20,20,20,.85);display:flex;align-items:center;padding:0 6px;gap:8px}
.controls .bar{flex:1;height:6px;background:#444;position:relative}
.controls .bar i{position:absolute;left:0;top:0;width:28%;height:100%;background:var(--accent-blue)}
.controls em{color:var(--accent-blue);font-size:8px;font-weight:700;font-style:italic}

.site-footer{position:absolute;left:0;top:1089px;width:967px;height:111px;background:var(--footer-bg)}
.footer-line{position:absolute;left:89px;top:33px;width:789px;border-top:1px solid var(--footer-line)}
.legal{position:absolute;left:89px;top:47px;font-size:10px;color:#333}
.address{position:absolute;left:91px;top:73px;font-size:10px;color:#444}
.newsletter{position:absolute;left:697px;top:45px;font-size:11.5px;color:#333}
.signup{position:absolute;left:696px;top:62px;width:185px;height:30px;background:#fff;border:1px solid #ccc;display:flex;align-items:center;padding-left:10px;font-size:8.5px;color:#444}
.signup span{position:absolute;right:4px;top:3px;width:44px;height:23px;background:var(--send);color:#fff;font-weight:700;text-align:center;line-height:23px;font-size:8px}
</style>
</head>
<body>
<header class="site-header">
  <div class="brand-mark">Bramblewood<br>Joinery</div>
  <div class="tagline">Kansas City's Premier Custom Kitchen Cabinet Design Company</div>
  <nav class="top-nav"><span>Home</span><span>Who We Are</span><span>Getting Started</span><span>Contact Us</span></nav>
  <div class="phone">
    <svg width="10" height="28" viewBox="0 0 10 28"><path d="M8 1H4Q1 1 1 5v18q0 4 3 4h4v-5H5V6h3z" fill="#fff"/></svg>
    <div><small>Call us on</small><b>555.014.2300</b></div>
  </div>
  <nav class="main-nav"><span>Customer Experience ▾</span><span>Professional ▾</span><span>Portfolio</span><span>Cabinet Hardware</span></nav>
  <svg class="arrow" style="left:53px" width="21" height="46" viewBox="0 0 21 46"><path d="M20 1L1 23l19 22" stroke="#fff" stroke-width="2" fill="none"/></svg>
  <svg class="arrow" style="left:897px" width="21" height="46" viewBox="0 0 21 46"><path d="M1 1l19 22L1 45" stroke="#fff" stroke-width="2" fill="none"/></svg>
  <div class="slider">
    <div class="slide-img" role="img" aria-label="Warm wood kitchen with cherry cabinets, range hood and granite counters"></div>
    <div class="slide-caption">Lorem ipsum dolor sit amet, consectetur adipiscing elit, sed do eiusmod &raquo;</div>
  </div>
  <div class="dots"><i></i><i class="on"></i><i></i><i></i><i></i><i></i></div>
</header>

<section class="cards">
  <div class="card"><div class="card-img" role="img" aria-label="White kitchen with arched hood and pendant lights" style="background:linear-gradient(180deg,#5f5048 0%,#9b8a7c 25%,#ece8e2 55%,#cfc6bb 75%,#6b5a4c 100%)"></div><div class="card-cap"><b>Lorem Ipsum &raquo;</b><span>Lorem ipsum dolor sit amet,consectetur</span></div></div>
  <div class="card"><div class="card-img" role="img" aria-label="Kitchen with dark island and white cabinets" style="background:linear-gradient(180deg,#ece9e3 0%,#c9c4bc 25%,#2e2e30 50%,#4a4644 72%,#6b4a32 100%)"></div><div class="card-cap"><b>Lorem Ipsum &raquo;</b><span>Lorem ipsum dolor sit amet,consectetur</span></div></div>
  <div class="card"><div class="card-img" role="img" aria-label="Kitchen with stainless wall oven and white cabinetry" style="background:linear-gradient(90deg,#3c3b3a 0%,#8e8c88 30%,#e3dfd7 55%,#cbb89e 78%,#8a6244 100%)"></div><div class="card-cap"><b>Lorem Ipsum &raquo;</b><span>Lorem ipsum dolor sit amet,consectetur</span></div></div>
</section>

<div class="news">
  <b>Latest News:</b>Lorem ipsum dolor sit amet, consectetur adipiscing elit, sed do eiusmod temporadipiscing elit,
  <a>&raquo; <u>Read News Item</u></a>
  <svg width="32" height="14" viewBox="0 0 32 14"><path d="M8 1L2 7l6 6M24 1l6 6-6 6" stroke="#111" stroke-width="2.5" fill="none"/></svg>
</div>

<section class="welcome">
  <h2>Welcome To <b>Bramblewood Joinery &amp; Fixtures</b></h2>
  <p>Established in 1966, Bramblewood Joinery has long stood as one of the Midwest's most renowned makers of custom cabinets and fixtures. Our handcrafted, award-winning creations have been chosen by hundreds of noteworthy homebuilders.</p>
  <p>And while we custom build cabinets, we built our business around the belief that our customers absolutely, unequivocally come first. From day one, our mission has been to help turn the houses that people live in to the homes they've always dreamed of.Beyond new homebuilders, everyone from remodelers to commercial clients have benefitted from our expert craftsmanship and impeccable quality.</p>
  <span class="btn">Read More</span>
</section>

<section class="video">
  <h2>Watch Our <b>Video</b></h2>
  <div class="video-frame">
    <div class="video-img" role="img" aria-label="Craftsman cutting a board at a table saw in a workshop"></div>
    <div class="side-tools">
      <span><svg width="12" height="11" viewBox="0 0 12 11"><path d="M6 10L1 5a2.6 2.6 0 0 1 5-3 2.6 2.6 0 0 1 5 3z" fill="#fff"/></svg></span>
      <span><svg width="12" height="12" viewBox="0 0 12 12"><circle cx="6" cy="6" r="5" stroke="#fff" stroke-width="1.4" fill="none"/><path d="M6 3v3h2.5" stroke="#fff" stroke-width="1.4" fill="none"/></svg></span>
      <span><svg width="12" height="12" viewBox="0 0 12 12"><circle cx="3" cy="6" r="1.6" fill="#fff"/><circle cx="9" cy="2.5" r="1.6" fill="#fff"/><circle cx="9" cy="9.5" r="1.6" fill="#fff"/><path d="M3 6l6-3.5M3 6l6 3.5" stroke="#fff"/></svg></span>
      <span><svg width="14" height="10" viewBox="0 0 14 10"><path d="M4 1L1 5l3 4M10 1l3 4-3 4M8 1L6 9" stroke="#fff" stroke-width="1.4" fill="none"/></svg></span>
    </div>
    <div class="controls">
      <svg width="12" height="12" viewBox="0 0 12 12"><path d="M2 1l9 5-9 5z" fill="#fff"/></svg>
      <div class="bar"><i></i></div>
      <em>HD</em>
    </div>
  </div>
</section>

<footer class="site-footer">
  <div class="footer-line"></div>
  <div class="legal">© Bramblewood Joinery 2015 &nbsp;|&nbsp; Terms &amp; Conditions &nbsp;|&nbsp; Privacy Policy</div>
  <div class="address">Bramblewood Joinery Dana Whitfield 4820 Orchard Lane Millbrook,</div>
  <div class="newsletter">Join Our Newsletter</div>
  <div class="signup">Enter Email Address<span>SEND</span></div>
</footer>
</body>
</html>
```